CLAIM SHIELD NETWORK

I'm virtually ready to launch my site, but I have a number of edits and modifications that need to be implemented. More importantly, I'm always looking to improve my site, particularly now that I am making my proverbial "FIRST IMPRESSION." Thus, I'm willing to see if there is someone who can add creativity and perhaps improve what I already have, particularly on the All Important Front Page.

```html
<!DOCTYPE html>
<html lang="en">
<head>
<meta charset="utf-8">
<title>Claim Shield Network</title>
<link href="https://fonts.googleapis.com/css2?family=Fira+Sans:wght@500;600;700&family=Roboto:wght@400;500;700&display=swap" rel="stylesheet">
<style>
:root{
  --navy:#0d2150;
  --navy-deep:#091838;
  --red:#b3121e;
  --red-dark:#8e0d17;
  --ink:#1d1d1f;
  --muted:#6d6d72;
  --line:#dcdcdc;
  --soft:#f4f4f4;
  --footer:#1b1b1d;
  --white:#fff;
}
*{box-sizing:border-box;margin:0;padding:0}
html,body{width:1200px;height:4087px;overflow:hidden}
body{position:relative;font-family:"Roboto",sans-serif;color:var(--ink);background:var(--white)}
.abs{position:absolute}
h1,h2,h3,.heading{font-family:"Fira Sans",sans-serif}

/* top bar */
.topbar{left:0;top:0;width:1200px;height:35px;background:var(--navy);color:#fff;font-size:11.5px;font-weight:500}
.topbar span{position:absolute;top:11px;display:flex;align-items:center;gap:8px}
.topbar i{width:7px;height:7px;border-radius:50%;background:var(--red);display:inline-block}

/* nav */
.nav{left:0;top:35px;width:1200px;height:79px;background:#fff}
.nav a{position:absolute;top:31px;font-size:13.5px;font-weight:500;color:var(--ink);text-decoration:none}
.nav .cta{top:19px;left:879px;width:176px;height:42px;border-radius:21px;background:var(--red);color:#fff;font-weight:700;display:flex;align-items:center;justify-content:center;font-size:13.5px}
.brand-badge{left:528px;top:2px;width:144px;height:144px;border-radius:50%;background:#fff;display:flex;align-items:center;justify-content:center;z-index:3}
.brand-badge div{width:120px;height:120px;border-radius:50%;background:var(--navy);color:#fff;display:flex;align-items:center;justify-content:center;text-align:center;font-family:"Fira Sans",sans-serif;font-weight:700;font-size:15px;line-height:1.15}

/* hero */
.hero-photo{left:0;top:114px;width:1200px;height:600px;background:linear-gradient(100deg,#e9eef2 0%,#cfd8df 35%,#6f5f55 60%,#2f2a2c 80%,#c9d0d6 100%)}
.hero-title{left:144px;top:222px;font-size:44px;font-weight:700;color:#111;letter-spacing:.5px}
.hero-sub{left:144px;top:292px;font-size:15px;color:#111}
.btn{display:flex;align-items:center;justify-content:center;gap:8px;border-radius:24px;color:#fff;font-weight:700;font-size:14px;text-transform:uppercase}
.btn .dot{width:14px;height:14px;border-radius:50%;background:#fff;position:relative}
.btn .dot::after{content:"";position:absolute;left:4px;top:4px;border-left:6px solid var(--red);border-top:3px solid transparent;border-bottom:3px solid transparent}
.hero-btn{left:144px;top:340px;width:327px;height:45px;background:var(--red)}
.hero-curve{left:0;top:500px;width:1200px;height:214px}

/* about */
.about-photo{left:143px;top:765px;width:444px;height:444px;border-radius:50%;background:linear-gradient(135deg,#5a3b2a,#2a1c16 60%,#4b4340)}
.about-badge{left:424px;top:1011px;width:190px;height:190px;border-radius:50%;background:#fff;display:flex;align-items:center;justify-content:center}
.about-badge div{width:172px;height:172px;border-radius:50%;background:var(--navy);border:8px solid var(--red);color:#fff;font-family:"Fira Sans",sans-serif;font-weight:700;font-size:17px;text-align:center;display:flex;align-items:center;justify-content:center;line-height:1.2}
.section-title{font-size:36px;font-weight:700;color:#111}
.rule{height:4px;background:var(--red)}
.about-title{left:656px;top:788px}
.about-rule{left:657px;top:836px;width:76px}
.about-text{left:656px;top:865px;width:400px;font-size:12.6px;line-height:23px;color:var(--muted);text-align:justify}
.about-text p+p{margin-top:13px}
.about-btn{left:656px;top:1117px;width:177px;height:50px;background:var(--red)}

/* services */
.services-bg{left:0;top:1285px;width:1200px;height:477px}
.services-title{left:0;top:1343px;width:1200px;text-align:center;color:#fff}
.services-rule{left:560px;top:1400px;width:80px}
.services-sub{left:0;top:1437px;width:1200px;text-align:center;color:#fff;font-size:15.5px;font-weight:500}
.services-sub s{color:var(--red)}
.card{background:#fff;border-radius:8px;box-shadow:0 4px 18px rgba(0,0,0,.18);text-align:center;padding:6px}
.card .ph{height:213px;border-radius:4px}
.card .ic{width:70px;height:70px;border-radius:50%;margin:-35px auto 0;border:4px solid #fff;display:flex;align-items:center;justify-content:center;position:relative}
.card h3{font-family:"Roboto",sans-serif;font-size:16px;font-weight:500;color:#111;margin-top:12px}
.card p{font-size:12.8px;line-height:21px;color:var(--muted);margin:10px 14px 0}
.card .btn{margin:20px auto 0;width:131px;height:40px;font-size:14px}
.arrow{width:40px;height:40px;border-radius:50%;display:flex;align-items:center;justify-content:center}

/* faq */
.faq-title{left:0;top:2045px;width:1200px;text-align:center}
.faq-title em{font-style:normal;color:var(--navy)}
.faq-rule{left:420px;top:2107px;width:360px}
.faq-intro{left:150px;top:2150px;width:900px;text-align:center;font-size:16px;font-weight:500;line-height:28px;color:#111}
.faq-item{left:211px;width:778px;height:51px;border:1px solid var(--line);border-radius:26px;box-shadow:0 2px 6px rgba(0,0,0,.08);font-size:15px;color:#222;display:flex;align-items:center;padding-left:22px;background:#fff}
.faq-item .chev{position:absolute;right:12px;top:15px;width:20px;height:20px;border-radius:50%;background:var(--navy)}
.faq-item .chev.open{background:var(--red)}
.faq-answer{left:232px;top:2370px;width:745px;font-size:12.8px;line-height:23px;color:var(--muted)}

/* contact */
.contact-bg{left:0;top:2715px;width:1200px;height:350px}
.contact-title{left:0;top:2765px;width:1200px;text-align:center;color:#fff;font-size:33px;font-weight:600}
.contact-rule{left:436px;top:2815px;width:328px;background:#fff}
.contact-lead{left:0;top:2849px;width:1200px;text-align:center;color:#fff;font-size:17px;font-weight:500}
.contact-small{left:280px;top:2888px;width:640px;text-align:center;color:#fff;font-size:12.6px;line-height:23px}
.call-btn{left:478px;top:2957px;width:246px;height:45px;border-radius:23px;background:#fff;color:var(--red);font-size:14px;font-weight:500;display:flex;align-items:center;padding-left:58px}
.call-btn .ph-ic{position:absolute;left:6px;top:5px;width:35px;height:35px;border-radius:50%;background:var(--red);display:flex;align-items:center;justify-content:center}

/* blog */
.blog-bg{left:0;top:3063px;width:1200px;height:620px;background:var(--soft)}
.blog-title{left:0;top:3128px;width:1200px;text-align:center}
.blog-title em{font-style:normal;color:var(--navy)}
.blog-rule{left:535px;top:3178px;width:130px}
.post{top:3230px;width:286px;height:333px;background:#fff}
.post .ph{height:166px}
.post h3{font-family:"Roboto",sans-serif;font-weight:500;font-size:15.5px;line-height:20px;margin:18px 20px 0;color:#111}
.post .meta{margin:14px 20px 0;font-size:12.6px;color:var(--muted);display:flex;gap:30px}
.post .meta b{display:inline-block;width:9px;height:9px;background:var(--navy);margin-right:6px;border-radius:2px}
.post p{margin:20px 20px 0;font-size:12.6px;line-height:22px;color:var(--muted)}

/* footer */
.footer-shape{left:0;top:3600px;width:1200px;height:487px}
.foot-logo{left:147px;top:3792px;width:160px;height:160px;border-radius:50%;background:#fff;display:flex;align-items:center;justify-content:center}
.foot-logo div{width:144px;height:144px;border-radius:50%;background:var(--navy);border:6px solid var(--red);color:#fff;font-family:"Fira Sans",sans-serif;font-weight:700;font-size:14px;text-align:center;display:flex;align-items:center;justify-content:center;line-height:1.2}
.socials{left:188px;top:3969px;display:flex;gap:8px}
.socials span{width:22px;height:22px;border-radius:50%;border:1.5px solid #fff}
.foot-col{top:3778px;color:#fff}
.foot-col h4{font-size:14.5px;font-weight:700;margin-bottom:26px}
.foot-col li{list-style:none;font-size:12.6px;line-height:26px}
.contact-row{display:flex;gap:12px;margin-bottom:14px;font-size:12.6px;line-height:19px}
.contact-row b{display:block;font-size:11px}
.contact-row i{width:11px;height:11px;background:var(--red);border-radius:2px;margin-top:3px;flex:none}
.foot-line{left:143px;top:4023px;width:912px;height:1px;background:#3b3b3d}
.copyright{left:0;top:4040px;width:1200px;text-align:center;color:#fff;font-size:13.5px}
.chat{left:1078px;top:4004px;width:32px;height:32px;border-radius:50%;background:var(--red)}
</style>
</head>
<body>

<div class="abs topbar">
  <span style="left:144px"><i></i>WWW.CLAIMSHIELDNETWORK.COM</span>
  <span style="left:369px"><i></i>(800) 555-0143</span>
  <span style="left:720px"><i></i>4820 Canyon Ridge Rd., Suite 210 Mesa, Arizona 85201</span>
</div>

<nav class="abs nav">
  <a style="left:144px">HOME</a>
  <a style="left:245px">ABOUT US</a>
  <a style="left:374px">OUR SERVICES</a>
  <a style="left:699px">FAQ</a>
  <a style="left:764px">CONTACT US</a>
  <a class="cta">FREE CONSULTATION</a>
</nav>
<div class="abs brand-badge"><div>CLAIM<br>SHIELD<br>NETWORK</div></div>

<section>
  <div class="abs hero-photo" role="img" aria-label="Photo of business professionals meeting in a bright office"></div>
  <h1 class="abs hero-title">CLAIM SHIELD NETWORK</h1>
  <p class="abs hero-sub">Our Unique Service Plan Makes It Possible For Us To Shield You From Claims.</p>
  <div class="abs btn hero-btn">Schedule Free Consultation <span class="dot"></span></div>
  <svg class="abs hero-curve" viewBox="0 0 1200 214" preserveAspectRatio="none">
    <path d="M0 70 Q600 260 1200 40 L1200 214 L0 214Z" fill="var(--navy)"/>
    <path d="M0 100 Q600 270 1200 70 L1200 214 L0 214Z" fill="var(--red)"/>
    <path d="M0 112 Q600 262 1200 88 L1200 214 L0 214Z" fill="#fff"/>
    <path d="M0 130 Q600 270 1200 110" stroke="var(--navy)" stroke-width="3" fill="none"/>
  </svg>
</section>

<section>
  <div class="abs about-photo" role="img" aria-label="Photo of a lawyer in a robe reading documents in a library"></div>
  <div class="abs about-badge"><div>CLAIM<br>SHIELD<br>NETWORK</div></div>
  <h2 class="abs section-title about-title">ABOUT US</h2>
  <div class="abs rule about-rule"></div>
  <div class="abs about-text">
    <p>A homebuilding company was sued by a former employee who claimed to have been promised a more favorable sales area, which claim was disputed by the homebuilder.</p>
    <p>There was no evidence that such a promise had been made, other than the plaintiff's oral testimony. The company had the case dismissed, but spent $10,000 defending the case.And even though it was awarded its attorney's fees, the plaintiff proved uncollectible. Had the company been an CSN member, the case likely would never have been filed.Call for your Free Consultation</p>
  </div>
  <div class="abs btn about-btn">Learn More <span class="dot"></span></div>
</section>

<section>
  <svg class="abs services-bg" viewBox="0 0 1200 477" preserveAspectRatio="none">
    <defs><linearGradient id="svcg" x1="0" x2="1"><stop offset="0" stop-color="#1c3263"/><stop offset=".5" stop-color="var(--navy)"/><stop offset="1" stop-color="#1c3263"/></linearGradient></defs>
    <path d="M0 50 Q600 -40 1200 50 L1200 477 L0 477Z" fill="url(#svcg)"/>
  </svg>
  <h2 class="abs section-title services-title">OUR SERVICES</h2>
  <div class="abs rule services-rule"></div>
  <p class="abs services-sub">The price for a membership is a ridiculously low <s>$9.95</s> PER WEEK. We believe that this fee is very affordable.</p>

  <div class="abs card" style="left:143px;top:1540px;width:289px;height:441px">
    <div class="ph" role="img" aria-label="Photo of hands signing a contract" style="background:linear-gradient(135deg,#e8e2d6,#b7a88e)"></div>
    <div class="ic" style="background:var(--navy)"><svg width="30" height="30" viewBox="0 0 24 24" fill="none" stroke="#fff" stroke-width="1.6"><path d="M3 11l9-7 9 7M5 10v10h14V10"/></svg></div>
    <h3>Proprietary Contract Language</h3>
    <p>CSN members are entitled to incorporate exclusive proprietary contract language in their contracts, work orders</p>
    <div class="btn" style="background:var(--navy)">Read More</div>
  </div>
  <div class="abs card" style="left:455px;top:1497px;width:289px;height:441px">
    <div class="ph" role="img" aria-label="Photo of a stressed businessman at his desk" style="background:linear-gradient(135deg,#7a8a6a,#c7c2b6)"></div>
    <div class="ic" style="background:var(--red)"><svg width="30" height="30" viewBox="0 0 24 24" fill="none" stroke="#fff" stroke-width="1.6"><rect x="5" y="4" width="14" height="16"/><path d="M8 9h8M8 13h8M8 17h5"/></svg></div>
    <h3>Free Attorney Letters</h3>
    <p>In addition to free monthly consultations, CSN members can have their local CSN Attorney send out a letter</p>
    <div class="btn" style="background:var(--red)">Read More</div>
  </div>
  <div class="abs card" style="left:768px;top:1540px;width:289px;height:441px">
    <div class="ph" role="img" aria-label="Photo of a judge's gavel on banknotes" style="background:linear-gradient(135deg,#8a6a4a,#b9c0b0)"></div>
    <div class="ic" style="background:var(--navy)"><svg width="30" height="30" viewBox="0 0 24 24" fill="none" stroke="#fff" stroke-width="1.6"><circle cx="12" cy="9" r="5"/><path d="M3 18h6l3 2h7"/></svg></div>
    <h3>Litigation Discounts</h3>
    <p>CSN members who use the Proprietary Contract Language described above are given considerable discounts</p>
    <div class="btn" style="background:var(--navy)">Read More</div>
  </div>
  <div class="abs arrow" style="left:72px;top:1735px;background:#222"><svg width="14" height="14" viewBox="0 0 14 14"><path d="M9 2L4 7l5 5" stroke="#fff" stroke-width="2" fill="none"/></svg></div>
  <div class="abs arrow" style="left:1088px;top:1735px;background:var(--red)"><svg width="14" height="14" viewBox="0 0 14 14"><path d="M5 2l5 5-5 5" stroke="#fff" stroke-width="2" fill="none"/></svg></div>
</section>

<section>
  <h2 class="abs section-title faq-title">FREQUENTLY <em>ASKED</em> QUESTIONS</h2>
  <div class="abs rule faq-rule"></div>
  <p class="abs faq-intro">CSN Is A Group Of Attorney And Legal Assistants With Many Years Of Experience In Litigation, Who Are Devoted To Preventing Legal Claims And Costly Lawsuits Through.</p>
  <div class="abs faq-item" style="top:2243px">Provide more details about the value of CSN's contract language.<span class="chev"></span></div>
  <div class="abs faq-item" style="top:2309px">Why should I be concerned about legal claims?<span class="chev open"></span></div>
  <p class="abs faq-answer">Lorem ipsum dolor sit amet, consectetur adipiscing elit. Suspendisse varius enim in eros elementum tristique. Duis cursus, mi quis viverra ornare, eros dolor interdum nulla, ut commodo diam libero vitae erat. Aenean faucibus nibh et justo cursus id rutrum lorem imperdiet. Nunc ut sem vitae risus tristique posuere.</p>
  <div class="abs faq-item" style="top:2457px">If I'm a contractor, how can an CSN membership minimize legal claims against my business?<span class="chev"></span></div>
  <div class="abs faq-item" style="top:2520px">What does an CSN membership cost?<span class="chev"></span></div>
  <div class="abs faq-item" style="top:2584px">Do you have a Referral Program?<span class="chev"></span></div>
</section>

<div class="abs blog-bg"></div>
<section>
  <svg class="abs contact-bg" viewBox="0 0 1200 350" preserveAspectRatio="none">
    <defs><linearGradient id="ctg" x1="0" x2="1"><stop offset="0" stop-color="var(--red-dark)"/><stop offset=".5" stop-color="var(--red)"/><stop offset="1" stop-color="var(--red-dark)"/></linearGradient></defs>
    <path d="M0 0H1200V265 Q600 420 0 265Z" fill="url(#ctg)"/>
  </svg>
  <h2 class="abs contact-title">CONTACT US FOR A FREE CONSULTATION</h2>
  <div class="abs rule contact-rule"></div>
  <p class="abs contact-lead">Contact us to find out how you can join us to CLAIM SHIELD NETWORK!!</p>
  <p class="abs contact-small">Contact Us For A Free Consultation And Receive A FREE OVERVIEW Of Your Business To See If You Are Truly Insulated From Legal Claims.</p>
  <div class="abs call-btn"><span class="ph-ic"><svg width="16" height="16" viewBox="0 0 24 24" fill="#fff"><path d="M6.6 10.8a15 15 0 006.6 6.6l2.2-2.2a1 1 0 011-.25 11.4 11.4 0 003.6.6 1 1 0 011 1V20a1 1 0 01-1 1A17 17 0 013 4a1 1 0 011-1h3.5a1 1 0 011 1 11.4 11.4 0 00.6 3.6 1 1 0 01-.25 1z"/></svg></span>CALL US (480) 555-0172</div>
</section>

<section>
  <h2 class="abs section-title blog-title">LATEST <em>BLOG</em></h2>
  <div class="abs rule blog-rule"></div>
  <article class="abs post" style="left:143px">
    <div class="ph" role="img" aria-label="Photo of scales of justice on a desk" style="background:linear-gradient(135deg,#d8d4cc,#7e746a)"></div>
    <h3>2021 Lorem ipsum dolor sit amet, consectetur adipiscing elit.</h3>
    <div class="meta"><span><b></b>by John Doe</span><span><b></b>Jun 24, 2020</span></div>
    <p>On June 24, 2020, sed do eiusmod tempor incididunt ut labore et.</p>
  </article>
  <article class="abs post" style="left:456px;box-shadow:0 4px 14px rgba(0,0,0,.15)">
    <div class="ph" role="img" aria-label="Photo of a lawyer addressing a courtroom" style="background:linear-gradient(135deg,#5b4030,#2a2220)"></div>
    <h3>2022 Lorem ipsum dolor sit amet, consectetur adipiscing elit.</h3>
    <div class="meta"><span><b></b>by John Doe</span><span><b></b>Jun 24, 2020</span></div>
    <p>On June 24, 2020, sed do eiusmod tempor incididunt ut labore et.</p>
  </article>
  <article class="abs post" style="left:769px">
    <div class="ph" role="img" aria-label="Photo of a business handshake" style="background:linear-gradient(135deg,#e8d9b8,#4b4a50)"></div>
    <h3>2023 Lorem ipsum dolor sit amet, consectetur adipiscing elit.</h3>
    <div class="meta"><span><b></b>by John Doe</span><span><b></b>Jun 24, 2020</span></div>
    <p>On June 24, 2020, sed do eiusmod tempor incididunt ut labore et.</p>
  </article>
</section>

<footer>
  <svg class="abs footer-shape" viewBox="0 0 1200 487" preserveAspectRatio="none">
    <path d="M0 60 Q600 -20 1200 60 L1200 487 L0 487Z" fill="var(--red)"/>
    <path d="M0 75 Q600 5 1200 75 L1200 487 L0 487Z" fill="#fff"/>
    <path d="M0 88 Q600 22 1200 88 L1200 487 L0 487Z" fill="var(--navy)"/>
    <path d="M0 130 Q600 40 1200 130 L1200 487 L0 487Z" fill="var(--footer)"/>
  </svg>
  <div class="abs foot-logo"><div>CLAIM<br>SHIELD<br>NETWORK</div></div>
  <div class="abs socials"><span></span><span></span><span></span></div>
  <div class="abs foot-col" style="left:430px"><h4>QUCIK LINKS</h4><ul><li>Home</li><li>About Us</li><li>Services</li><li>Faq</li></ul></div>
  <div class="abs foot-col" style="left:611px"><h4>ABOUT COMPANY</h4><ul><li>Privacy Policy</li><li>Terms of Service</li><li>Contact Us</li></ul></div>
  <div class="abs foot-col" style="left:843px"><h4>CONTACT US</h4>
    <div class="contact-row"><i></i><div><b>Phone</b>800.555.0188</div></div>
    <div class="contact-row"><i></i><div><b>Email</b>info@claimshieldnetwork.net</div></div>
    <div class="contact-row"><i></i><div><b>Location</b>4820 Canyon Ridge Rd.<br>Suite 210, Mesa, Arizona 85201</div></div>
  </div>
  <div class="abs foot-line"></div>
  <p class="abs copyright">Copyright© 2023 Claimshieldnetwork.net | All Rights Reserved</p>
  <div class="abs chat"></div>
</footer>

</body>
</html>
```